Bright Harbor Charity - helping the disadvantaged

I would like a new web site design for my charity BRIGHT HARBOR. The charity provides help for the disadvantaged. See current site
brightharbor.org.au for details. Please refer to the current site for information on the charity. The objectives of the charity are in the "about us" tab. You will also notice on the site that we provide information about events that we sponsor an area for this should be provided on the site.

Target Market(s)

We have two targets:
1. Individuals and Businesses that will donate money to the charity.
2. Individuals that are in need of support from the charity.

Industry/Entity Type

Charity

Requirements
Must have
• Ability for individuals to be able to understand the type of support we can provide.
Nice to have
• Our logo should be prominate on each pages
Should not have
• Should be use modern fonts

```html
<!DOCTYPE html>
<html lang="en">
<head>
<meta charset="utf-8">
<title>Bright Harbor — Helping the Disadvantaged</title>
<link rel="stylesheet" href="https://fonts.googleapis.com/css2?family=Source+Sans+3:wght@400;600&family=Cinzel:wght@400&display=swap">
<style>
:root{
  --green:#6a9a1e;
  --green-dark:#4f7d12;
  --green-btn:#5e9c1c;
  --orange:#f7a833;
  --orange-dark:#ef8f17;
  --brown:#5d5452;
  --text:#4a4a4a;
  --muted:#6b6b6b;
  --line:#d5d5d5;
  --nav:#f2f2f2;
  --footer:#ebebeb;
  --white:#ffffff;
  --yellow:#f7b514;
}
*{box-sizing:border-box;margin:0;padding:0}
html,body{width:1200px;height:2361px;overflow:hidden}
body{position:relative;background:var(--white);font-family:"Source Sans 3",Arial,sans-serif;color:var(--text)}
.abs{position:absolute}

/* top bar */
.topbar{left:0;top:0;width:1200px;height:35px;background:#e3e3e3}
.top-btn{top:0;height:43px;width:107px;background:linear-gradient(#72b42a,var(--green-dark));color:#fff;font-size:17px;display:flex;align-items:center;justify-content:center;border-radius:0 0 8px 8px;box-shadow:0 2px 4px rgba(0,0,0,.25);letter-spacing:.5px}

/* brand */
.brand{left:0;top:95px;width:1200px;height:80px;display:flex;align-items:center;justify-content:center}
.brand-rule{position:absolute;top:142px;height:1px;background:#cfcfcf}
.brand-name{font-size:58px;font-weight:600;color:var(--green);letter-spacing:1px;background:#fff;padding:0 10px;position:relative}

/* navigation */
.nav{left:0;top:208px;width:1200px;height:67px;background:linear-gradient(#fafafa,#e6e6e6);border-top:1px solid #dcdcdc}
.nav a{position:absolute;top:0;height:67px;display:flex;align-items:center;justify-content:center;font-size:17px;color:#444;text-decoration:none;border-right:1px solid #d0d0d0}
.nav a:last-child{border-right:none}

/* hero */
.hero{left:0;top:275px;width:1200px;height:437px;background:linear-gradient(var(--orange),var(--orange-dark))}
.hero-frame{left:31px;top:287px;width:1137px;height:370px;background:#fff;padding:10px;box-shadow:0 4px 10px rgba(0,0,0,.25)}
.hero-sky{left:41px;top:297px;width:1117px;height:350px;background:linear-gradient(180deg,#8cc3ef 0%,#cfe6f8 55%,#f0f6fb 100%)}
.hero-card{left:47px;top:327px;width:449px;height:267px;background:rgba(255,255,255,.95);padding:55px 30px 0 30px}
.hero-title{font-family:"Cinzel",Georgia,serif;font-size:30px;color:#2b2b2b;line-height:1}
.hero-title span{color:var(--green)}
.hero-copy{font-size:13.5px;line-height:21px;color:#333;margin-top:16px}
.btn-donate{display:inline-block;margin-top:14px;background:var(--yellow);color:#fff;font-size:15px;padding:8px 12px;border-radius:4px}
.hero-poster{left:555px;top:295px;width:602px;height:330px;background:linear-gradient(180deg,#3f8fe0 0%,#9fd0f4 45%,#f5f7e6 75%,#7fc24a 100%);border:5px solid #fff;box-shadow:0 2px 6px rgba(0,0,0,.3)}
.slide-arrow{top:446px;width:24px;height:34px;background:rgba(255,255,255,.85);border-radius:3px;display:flex;align-items:center;justify-content:center}
.dots{left:519px;top:669px;width:154px;height:29px;background:var(--orange-dark);border-radius:15px;display:flex;align-items:center;justify-content:center;gap:6px;box-shadow:inset 0 1px 3px rgba(0,0,0,.2)}
.dots i{width:9px;height:9px;border-radius:50%;background:#fff;display:block}

/* section tabs */
.tab{height:52px;color:#fff;font-size:21px;display:flex;align-items:center;padding-left:22px;letter-spacing:.5px}
.tab svg{position:absolute;left:0;top:0}
.tab span{position:relative}
.tab-rule{height:0;border-top:2px dotted #c8c8c8}

.body-copy{font-size:12.5px;line-height:23.6px;color:var(--text)}

/* blog */
.blog{left:836px;top:755px;width:338px;height:358px;background:linear-gradient(90deg,#f1f1f1,#fafafa)}
.blog-item{left:868px;width:300px}
.blog-date{font-size:18px;color:#555}
.blog-text{font-size:12.5px;line-height:20px;color:#666;margin-top:8px}
.btn-view{left:864px;top:1062px;width:109px;height:27px;background:#d9d9d9;border-radius:14px;font-size:13px;color:#555;display:flex;align-items:center;justify-content:center}

/* announcements */
.ann-title{font-size:20px;color:#222}
.ann-rule{height:1px;background:var(--line)}
.ann-image{border:2px solid #ddd;padding:6px;background:#fff}
.ann-image div{width:100%;height:100%}

.gallery-title{left:35px;top:1645px;font-size:20px;color:#222}
.thumb{top:1696px;width:268px;height:188px;border:4px solid #e0e0e0;box-shadow:0 1px 3px rgba(0,0,0,.2)}

/* footer */
.footer{left:0;top:1973px;width:1200px;height:388px;background:var(--footer)}
.foot-title{font-size:19px;color:#333}
.foot-links{font-size:13.5px;color:#555;list-style:none}
.foot-links li{position:absolute;white-space:nowrap;padding-left:16px}
.foot-links li::before{content:"";position:absolute;left:0;top:5px;border-left:6px solid #888;border-top:4px solid transparent;border-bottom:4px solid transparent}
.social{top:2071px;width:44px;height:44px;border-radius:50%;box-shadow:0 2px 4px rgba(0,0,0,.3)}
.email{left:734px;top:2075px;width:246px;height:34px;background:#fff;border:1px solid #ddd;font-size:13px;font-style:italic;color:#aaa;padding:8px 14px}
.btn-sub{left:983px;top:2075px;width:103px;height:34px;background:var(--yellow);color:#fff;font-size:14px;display:flex;align-items:center;justify-content:center}
.copyright{left:37px;top:2295px;font-size:13px;color:#666}
</style>
</head>
<body>

<div class="abs topbar"></div>
<div class="abs top-btn" style="left:932px">LOG IN</div>
<div class="abs top-btn" style="left:1044px">SUPPORT</div>

<div class="abs brand-rule" style="left:150px;width:900px"></div>
<div class="abs brand"><div class="brand-name">BRIGHT HARBOR</div></div>

<nav class="abs nav">
  <a style="left:31px;width:107px">HOME</a>
  <a style="left:138px;width:133px">ABOUT US</a>
  <a style="left:271px;width:118px">DONATE</a>
  <a style="left:389px;width:97px">APPLY</a>
  <a style="left:486px;width:114px">PLEDGE</a>
  <a style="left:600px;width:132px">NOMINATE</a>
  <a style="left:732px;width:118px">EVENTS</a>
  <a style="left:850px;width:153px">CONTACT US</a>
  <a style="left:1003px;width:154px">DIRECTORS</a>
</nav>

<section class="abs hero"></section>
<div class="abs hero-frame"></div>
<div class="abs hero-sky" role="img" aria-label="Sky with soft clouds background"></div>
<div class="abs hero-card">
  <h1 class="hero-title"><span>BRIGHT HARBOR</span> PUNCH LINE</h1>
  <p class="hero-copy">Static website are cheaper and also it needs less maintenance too. It's the simplest, cheapest and also the basic thing the search engine picks it up very easily. We at Lumen Works provide you the best simple websites too with total work done</p>
  <span class="btn-donate">DONATE NOW</span>
</div>
<div class="abs hero-poster" role="img" aria-label="Event poster: Saturday 24th March at Fernvale Learning Centre, 10am till 3pm, free community activities"></div>
<div class="abs slide-arrow" style="left:560px"><svg width="12" height="18"><path d="M9 2 3 9l6 7" fill="none" stroke="#777" stroke-width="2.5"/></svg></div>
<div class="abs slide-arrow" style="left:1128px"><svg width="12" height="18"><path d="M3 2l6 7-6 7" fill="none" stroke="#777" stroke-width="2.5"/></svg></div>
<div class="abs dots"><i></i><i></i><i></i><i></i><i></i></div>

<!-- welcome -->
<div class="abs tab" style="left:30px;top:755px;width:330px">
  <svg width="330" height="52"><path d="M0 0H330L310 52H0Z" fill="#5d5452"/></svg>
  <span>WELCOME TO BRIGHT HARBOR</span>
</div>
<div class="abs tab-rule" style="left:360px;top:787px;width:456px"></div>
<div class="abs body-copy" style="left:31px;top:826px;width:790px">
  <p>Static website is a simple way to get your message out to the public. Static website are cheaper and also it needs less maintenance too. It's the simplest, cheapest and also the basic thing the search engine picks it up very easily. We at Lumen Works provide you the best simple websites too with total work done as using all the best designing and all done so that you can achieve the goal of yours through our work done on your website.</p>
  <p style="margin-top:6px">We have learnt that designing is not only inclined to powerful imaginations but also focused and attractive to expected viewers also. At Lumenworks Studio we use all the latest technologies for web designing. Lumenworks Studio provides the best web designing which compels the customers to ask and inquire about. We ensure that our designs represent the client area to perfection and look convincing to the targeted audience as well. We believe that you need us to represent beautifully the unique way of your doing the business. We design user-friendly website that forces the viewer to return to the website again and again. The company has some of the finest talents in industry.</p>
</div>

<!-- blog -->
<aside class="abs blog"></aside>
<div class="abs tab" style="left:836px;top:759px;width:296px">
  <svg width="296" height="52"><path d="M0 0H296L276 52H0Z" fill="#5d5452"/></svg>
  <span>RECENT BLOG &amp; NEWS</span>
</div>
<div class="abs blog-item" style="top:836px">
  <div class="blog-date">20.March.2012</div>
  <div class="blog-text">Lumen Works provide you the best simple websites too with total work done as using all the best designing and all done so that you can</div>
</div>
<div class="abs ann-rule" style="left:852px;top:943px;width:310px"></div>
<div class="abs blog-item" style="top:955px">
  <div class="blog-date">16.March.2012</div>
  <div class="blog-text">Lumen Works provide you the best simple websites too with total work done as using all the best designing and all done so that you can</div>
</div>
<div class="abs btn-view">VIEW ALL</div>

<!-- announcements -->
<div class="abs tab" style="left:30px;top:1101px;width:295px">
  <svg width="295" height="56"><path d="M0 0H295L275 56H0Z" fill="#5d5452"/></svg>
  <span>ANNOUNCEMENTS</span>
</div>
<div class="abs tab-rule" style="left:325px;top:1135px;width:760px"></div>

<div class="abs ann-title" style="left:31px;top:1192px">Unity Day Information Sheet &amp; Booking Form</div>
<div class="abs ann-rule" style="left:31px;top:1226px;width:535px"></div>
<div class="abs ann-image" style="left:31px;top:1239px;width:535px;height:217px"><div role="img" aria-label="Unity Day banner with a row of paper cut-out figures" style="background:linear-gradient(180deg,#0a0a0a 0%,#1a1a1a 55%,#f0a21e 56%,#f0a21e 70%,#111 71%,#3a6fb0 100%)"></div></div>
<p class="abs body-copy" style="left:31px;top:1473px;width:545px">We have learnt that designing is not only inclined to powerful imaginations but also focused and attractive to expected viewers also. At Lumenworks Studio we use all the latest technologies for web designing. Lumenworks Studio provides the best web designing which compels the customers to ask and inquire about.</p>

<div class="abs ann-title" style="left:606px;top:1192px">Unity Day</div>
<div class="abs ann-rule" style="left:606px;top:1226px;width:547px"></div>
<div class="abs ann-image" style="left:606px;top:1239px;width:547px;height:217px"><div role="img" aria-label="Colourful row of paper cut-out figures holding hands above a slogan" style="background:linear-gradient(180deg,#7fc7c0 0%,#e8a860 30%,#f7f3f5 55%,#f7f3f5 100%)"></div></div>
<p class="abs body-copy" style="left:610px;top:1473px;width:545px">We have learnt that designing is not only inclined to powerful imaginations but also focused and attractive to expected viewers also. At Lumenworks Studio we use all the latest technologies for web designing. Lumenworks Studio provides the best web designing which compels the customers to ask and inquire about.</p>

<!-- gallery -->
<div class="abs gallery-title">Art Exhibition</div>
<div class="abs ann-rule" style="left:31px;top:1678px;width:1128px"></div>
<div class="abs thumb" style="left:31px;background:linear-gradient(135deg,#e5452b,#f2a23a 40%,#2d6fb8 75%,#1b2a55)" role="img" aria-label="Vivid painting of a musician"></div>
<div class="abs thumb" style="left:319px;background:linear-gradient(135deg,#e3d6c2,#a89a88 50%,#6b5e52)" role="img" aria-label="Sculpture of interlocking staircases"></div>
<div class="abs thumb" style="left:604px;background:linear-gradient(135deg,#2f7ed8,#e8c43a 40%,#d8452f 70%,#6d3f9a)" role="img" aria-label="Colourful painting of city buildings"></div>
<div class="abs thumb" style="left:891px;background:linear-gradient(135deg,#c93b3b,#3d77b8 40%,#e6b83a 70%,#2d2d5a)" role="img" aria-label="Abstract colourful mural"></div>

<!-- footer -->
<footer class="abs footer"></footer>
<svg class="abs" style="left:0;top:1963px" width="1200" height="12">
  <path d="M0 12 Q15 0 30 12 Q45 0 60 12 Q75 0 90 12 Q105 0 120 12 Q135 0 150 12 Q165 0 180 12 Q195 0 210 12 Q225 0 240 12 Q255 0 270 12 Q285 0 300 12 Q315 0 330 12 Q345 0 360 12 Q375 0 390 12 Q405 0 420 12 Q435 0 450 12 Q465 0 480 12 Q495 0 510 12 Q525 0 540 12 Q555 0 570 12 Q585 0 600 12 Q615 0 630 12 Q645 0 660 12 Q675 0 690 12 Q705 0 720 12 Q735 0 750 12 Q765 0 780 12 Q795 0 810 12 Q825 0 840 12 Q855 0 870 12 Q885 0 900 12 Q915 0 930 12 Q945 0 960 12 Q975 0 990 12 Q1005 0 1020 12 Q1035 0 1050 12 Q1065 0 1080 12 Q1095 0 1110 12 Q1125 0 1140 12 Q1155 0 1170 12 Q1185 0 1200 12 Z" fill="#ebebeb"/>
</svg>

<div class="abs foot-title" style="left:43px;top:2020px">Some of Our Quick Links</div>
<div class="abs ann-rule" style="left:43px;top:2050px;width:330px"></div>
<ul class="foot-links">
  <li class="abs" style="left:43px;top:2081px">Main page</li>
  <li class="abs" style="left:43px;top:2114px">About Our Company</li>
  <li class="abs" style="left:43px;top:2148px">Services Overview</li>
  <li class="abs" style="left:43px;top:2179px">Support &amp; FAQ</li>
  <li class="abs" style="left:43px;top:2213px">Contact Infromation</li>
  <li class="abs" style="left:232px;top:2081px">Best Donation</li>
  <li class="abs" style="left:232px;top:2114px">Donate Now</li>
  <li class="abs" style="left:232px;top:2148px">Recent Blog &amp; New</li>
  <li class="abs" style="left:232px;top:2179px">Testimonials</li>
</ul>

<div class="abs foot-title" style="left:464px;top:2020px">Get In Touch</div>
<div class="abs ann-rule" style="left:464px;top:2050px;width:240px"></div>
<div class="abs social" style="left:464px;background:#3b5fa6"></div>
<div class="abs social" style="left:513px;background:#3aa6d8"></div>
<div class="abs social" style="left:564px;background:#d93a2f"></div>
<div class="abs" style="left:470px;top:2133px;font-size:13.5px;color:#555">Circlebook &nbsp;|&nbsp; Chirper &nbsp;|&nbsp; ClipTube</div>

<div class="abs foot-title" style="left:734px;top:2020px">Sign Up For Our Newsletters</div>
<div class="abs ann-rule" style="left:734px;top:2050px;width:420px"></div>
<div class="abs email">Enter your email address</div>
<div class="abs btn-sub">SUBSCRIBE</div>

<div class="abs ann-rule" style="left:37px;top:2274px;width:1126px;background:#cfcfcf"></div>
<div class="abs copyright">Copyright © 2012 Company Name &nbsp;|&nbsp; All right reserved</div>

</body>
</html>
```